"Velmora Crest" sexual performance enhancement pill bottle label needed.

This should be interesting...

I am starting a line of sexual performance enhancement products. This will be the first of several products basically. Keep in mind, I am the type of business person to stay with one company for years if they provide me with quality work.

This particular product is a male sexual performance pill. The name of the product is "Velmora Crest." The packaging of the pills are a black bottle with a white top. Label on the product example would be perfect but at a minimum I have attached a "template" for your guidance.

Some of the technical aspects of this are as follows:

-File Format: Illustrator CS6 is preferred. (Winner must provide artwork in layer and can not flatten artwork.)
-Resolution: 300 dpi minimum
-Bleed: 1/16th (0.0625") inch from edge of label
-Color Mode: CMYK only or must be converted to CMYK for final production

Lastly, this is your project as a designer, artist, creator, this is essentially a piece of you that will be sold and known by thousands of people. I have no color scheme that I prefer, just use the template and follow the layout. If you have any further questions, please feel free to contact me at any time.
Updates

Quick note on the product and what it does: -Powerful, long lasting, harder erections -Works in a minutes and last for hours -Enhances sexual desire and drive Thank you for your ideas...

Project Deadline Extended
Reason: We decided to extent the project for a few more days to let the last few concepts come in. So far things are looking really good and we definitely have seen some amazing designs. Thank you for your hard work and amazing creativity. Looking forward to seeing what we have come in the next couple of day. Very respectfully, Brev

ONLY THREE DAYS LEFT!!!! Please submit your ideas as soon as possible. And as always, thank you for your help!!! V/r, Brev

Industry/Entity Type

Graphic Design

```html
<!DOCTYPE html>
<html lang="en">
<head>
<meta charset="utf-8">
<title>Velmora Crest – Bottle Label</title>
<link href="https://fonts.googleapis.com/css2?family=Anton&family=Roboto+Condensed:wght@400;700&display=swap" rel="stylesheet">
<style>
  :root{
    --ink:#000000;
    --mint:#5ff5b2;
    --paper:#ffffff;
    --text:#ffffff;
  }
  *{margin:0;padding:0;box-sizing:border-box}
  html,body{width:1200px;height:1001px;overflow:hidden;background:var(--paper)}
  .canvas{position:relative;width:1200px;height:1001px;background:var(--paper);font-family:"Roboto Condensed",Arial,sans-serif}
  .label{position:absolute;left:192px;top:84px;width:821px;height:322px;background:var(--ink);color:var(--text)}
  .abs{position:absolute}

  /* left panel */
  .usage{left:28px;top:46px;width:232px;font-size:7.6px;line-height:1.28;text-align:justify}
  .usage b{color:var(--mint);font-weight:700}
  .warning{left:28px;top:172px;width:232px;font-size:7.6px;line-height:1.28;font-weight:700;color:var(--mint)}
  .disclaimer{left:28px;top:208px;width:232px;height:40px;border:1.5px solid var(--text);padding:4px 8px;font-size:6.8px;line-height:1.3}
  .maker{left:28px;top:260px;display:flex;gap:12px;align-items:flex-start}
  .maker-name{font-family:"Anton",sans-serif;font-size:10px;line-height:1;color:var(--mint);width:26px;text-align:center}
  .maker-info{font-size:5px;line-height:1.5;font-weight:700}
  .maker-info .web{color:var(--mint)}

  /* centre panel */
  .brand{left:270px;top:60px;width:280px;text-align:center;font-family:"Anton",sans-serif;font-size:64px;line-height:1;color:var(--mint);letter-spacing:1px}
  .strength-count{left:327px;top:191px;font-family:"Anton",sans-serif;font-size:12px;color:var(--text);letter-spacing:.5px}
  .claim{left:423px;top:190px;font-size:13px;color:var(--text);letter-spacing:.3px}
  .max-bar{left:290px;top:249px;width:260px;height:32px;display:flex;align-items:center;gap:4px}
  .max-bar .stripe{width:3px;height:32px;background:var(--mint)}
  .max-bar .stripes{display:flex;gap:4px}
  .max-bar .badge{flex:1;height:26px;margin:0 4px;background:var(--mint);color:var(--ink);font-family:"Anton",sans-serif;font-size:17px;display:flex;align-items:center;justify-content:center;letter-spacing:.5px}
  .count{left:270px;top:292px;width:280px;text-align:center;font-size:11px;font-weight:700;letter-spacing:.2px}

  /* right panel */
  .facts{left:583px;top:48px;width:202px;height:197px;border:2px solid var(--text);padding:7px 8px}
  .facts h2{font-family:"Roboto Condensed",sans-serif;font-size:19px;font-weight:700;color:var(--mint);line-height:1.05}
  .facts .serving{font-size:9px;line-height:1.25;margin-top:3px}
  .facts .rule-thick{height:5px;background:var(--text);margin:4px 0}
  .facts .rule-thin{height:1px;background:var(--text);margin:3px 0}
  .facts .head{display:flex;justify-content:space-between;font-size:8px;margin:3px 0}
  .facts .formula{font-size:8.5px;font-weight:700;color:var(--mint)}
  .facts .ingredients{font-size:6.6px;line-height:1.35;font-weight:700}
  .facts .foot{font-size:9px;font-weight:700;margin-top:3px}
  .other{left:590px;top:253px;width:210px;font-size:6.8px;line-height:1.4;font-weight:700}
  .other b{color:var(--mint)}
</style>
</head>
<body>
<div class="canvas">
  <section class="label">
    <div class="abs usage">
      <b>SUGGESTED USE:</b> As a dietary supplement, take two (2) capsules 1 hour before physical activity, or as directed by your health care professional. Do not exceed two (2) capsules daily.<br>
      <b>CAUTION:</b> Do not exceed recommended dose. This product is not intended for pregnant or nursing mothers, children under the age of 18, or individuals taking prescription drugs. Discontinue use immediately if nausea, sleeplessness, or nervousness occur. Do not take this product if you have a known medical condition including high blood pressure, diabetes, any cardiovascular disorder, heart disease, hyperthyroidism, or are taking anti-depressant medications. If you have questions about the advisability of taking this product, consult your physician prior to use.
    </div>
    <div class="abs warning">KEEP OUT OF THE REACH OF CHILDREN. DO NOT USE IF SAFETY SEAL IS DAMAGED OR MISSING. STORE AT ROOM TEMPERATURE.</div>
    <div class="abs disclaimer">* These statements have not been evaluated by the Food and Drug Administration. This product is not intended to diagnose, treat, cure or prevent any disease.</div>
    <div class="abs maker">
      <div class="maker-name">VELMORA CREST</div>
      <div class="maker-info">
        Manufactured Exclusively For:<br>
        1200 Sample Way, Suite 4, PA<br>
        P: 555.010.0100 &nbsp;F: 555.010.0199<br>
        <span class="web">www.velmoracrest.com</span>
      </div>
    </div>

    <div class="abs brand">VELMORA<br>CREST</div>
    <div class="abs strength-count">1600</div>
    <div class="abs claim">PURE AND POTENT*</div>
    <div class="abs max-bar">
      <div class="stripes"><span class="stripe"></span><span class="stripe"></span><span class="stripe"></span></div>
      <div class="badge">MAX STRENGTH!</div>
      <div class="stripes"><span class="stripe"></span><span class="stripe"></span><span class="stripe"></span></div>
    </div>
    <div class="abs count">DIETARY SUPPLEMENT · 60 CAPSULES</div>

    <div class="abs facts">
      <h2>Supplement Facts</h2>
      <div class="serving">Serving Size: 2 Capsules<br>Servings Per Container: 30</div>
      <div class="rule-thick"></div>
      <div class="head"><span>Amount Per Serving</span><span>% Daily Value</span></div>
      <div class="rule-thick"></div>
      <div class="formula">VCX-Rx™ Proprietary Formula 1,560 mg †</div>
      <div class="ingredients">Horny Goat Weed (herb powder), Maca (herb powder), Macuna Pruriens (L-Dopa), Polypodium Vulgare (herb powder), Yohimbe Bark (herb powder), Saw Palmetto (herb powder), Muira Puama (herb powder), Arginine (L-Arginine hydrochloride), Panax Ginseng (herb powder).</div>
      <div class="rule-thick"></div>
      <div class="foot">† % Daily Value not established</div>
    </div>
    <div class="abs other"><b>OTHER INGREDIENTS:</b> Gelatin, Magnesium Stearate, and Calcium Carbonate.</div>
  </section>
</div>
</body>
</html>
```